Design a Website for an IT Support Company

We are an IT support company that provides commercial IT support and services to small and medium sized businesses. We are in need of a website to be developed for our business.
We would like to work with someone who is either familiar with the IT field, or has developed a website for an IT support company in the past.
Some examples of designs/layouts that we like:
https://www.veldaworks.example/
http://www.marsbyquill.example/
http://817kq.example/
http://www.olbenstructures.example/
http://www.bykq.example/
I have attached a word document that gives a menu system/page layout format that we would like for our website as well as branch office phone numbers. Our logo is also attached that you can use for your design purposes. We currently do not have copy produced for all of the pages outlined in the word document, but would get this done during the project with the selected designer.
We would like the website to be SEO friendly & fully responsive. We would prefer a Wordpress format, however, we are open to HTML formats as well.

```html
<!DOCTYPE html>
<html lang="en">
<head>
<meta charset="utf-8">
<title>Corvane IT – IT Support for Small and Medium Businesses</title>
<link href="https://fonts.googleapis.com/css2?family=Open+Sans:ital,wght@0,400;0,600;0,700;0,800;1,400&display=swap" rel="stylesheet">
<style>
:root{
  --blue:#1a73c4;
  --blue-dark:#145ea3;
  --ink:#2b2b2b;
  --text:#444;
  --muted:#777;
  --light:#f1f1f1;
  --dark:#2d2d2d;
  --darker:#1f1f1f;
  --green:#3aa420;
  --white:#fff;
}
*{box-sizing:border-box;margin:0;padding:0}
html,body{width:1200px;height:3673px;overflow:hidden}
body{font-family:"Open Sans",Arial,sans-serif;color:var(--text);background:var(--white);position:relative}
.abs{position:absolute}
.section-title{position:absolute;left:0;width:1200px;text-align:center;font-weight:700;font-size:27px;letter-spacing:.5px;color:var(--ink);text-transform:uppercase}

/* header */
.site-header{position:absolute;left:0;top:0;width:1200px;height:122px;background:var(--white)}
.brand{position:absolute;left:74px;top:24px;display:flex;align-items:center;gap:12px}
.brand-dot{width:44px;height:44px;border-radius:50%;background:var(--blue)}
.brand-name{font-weight:700;font-size:34px;color:var(--ink)}
.header-cta{position:absolute;left:510px;top:18px;width:390px;height:40px;border:2px solid #bcbcbc;color:var(--green);font-size:14px;font-weight:600;display:flex;align-items:center;justify-content:center;text-transform:uppercase}
.header-phone{position:absolute;left:925px;top:18px;display:flex;align-items:center;gap:12px;color:var(--blue);font-weight:600;font-size:24px}
.phone-badge{width:36px;height:36px;border-radius:50%;background:#6b6b6b;display:flex;align-items:center;justify-content:center}
.main-nav{position:absolute;left:680px;top:82px;display:flex;gap:0}
.main-nav a{display:block;text-decoration:none;color:var(--ink);font-weight:700;font-size:15px;padding:0 22px 10px;text-transform:uppercase}
.main-nav a.active{color:var(--blue);border-bottom:3px solid var(--blue)}

/* hero */
.hero{position:absolute;left:0;top:122px;width:1200px;height:554px;background:linear-gradient(100deg,#8d8f92 0%,#c9cbcd 35%,#e6e7e8 60%,#b7b9bb 100%)}
.hero-caption{position:absolute;left:73px;top:196px;width:569px;height:164px;background:rgba(20,20,20,.82);padding:12px 24px}
.hero-caption h1{font-size:37px;font-weight:800;color:var(--white);line-height:1.1;text-transform:uppercase}
.hero-caption h1 span{color:var(--blue)}
.hero-caption p{color:var(--white);font-weight:600;font-size:21px;line-height:1.4;margin-top:8px}
.hero-dots{position:absolute;left:572px;top:518px;display:flex;gap:8px}
.hero-dots i{width:12px;height:12px;border-radius:50%;background:rgba(255,255,255,.7)}
.hero-dots i.on{background:var(--blue)}

/* services */
.service-card{position:absolute;top:774px;width:331px;height:340px;background:var(--white);box-shadow:0 4px 14px rgba(0,0,0,.16);padding:30px 24px}
.service-head{display:flex;align-items:center;gap:22px;height:56px}
.service-head h3{color:var(--blue);font-size:24px;font-weight:700;text-transform:uppercase}
.service-list{list-style:none;margin-top:18px}
.service-list li{font-size:15px;color:var(--text);line-height:29.5px;display:flex;align-items:center;gap:14px}
.tick{width:14px;height:14px;flex:none}
.btn-small{display:inline-block;margin-top:12px;background:var(--blue);color:var(--white);font-size:13px;font-weight:700;padding:9px 14px;text-transform:uppercase}

/* welcome */
.welcome{position:absolute;left:0;top:1166px;width:1200px;height:365px;background:var(--dark)}
.welcome-photo{position:absolute;left:0;top:0;width:588px;height:365px;background:linear-gradient(120deg,#b8c2cc 0%,#e4e8ec 45%,#8e9aa6 100%);clip-path:polygon(0 0,100% 0,545px 100%,0 100%)}
.welcome-copy{position:absolute;left:642px;top:64px;width:470px;color:#ddd}
.welcome-copy h2{font-size:27px;font-weight:700;color:var(--white);text-transform:uppercase}
.welcome-copy p{font-size:15px;line-height:1.75;margin-top:18px}
.btn{display:inline-block;background:var(--blue);color:var(--white);font-weight:700;font-size:15px;padding:14px 32px;text-transform:uppercase;margin-top:26px}

/* why */
.why{position:absolute;left:0;top:1531px;width:1200px;height:820px;background:var(--blue)}
.why .section-title{color:var(--white);top:48px}
.video-frame{position:absolute;left:287px;top:105px;width:624px;height:367px;border:6px solid #5aa3e0;background:linear-gradient(135deg,#6f9448 0%,#c9d6b8 45%,#e9ece4 70%,#8fa873 100%)}
.play{position:absolute;left:282px;top:150px}
.feature{position:absolute;top:526px;width:358px;height:233px;text-align:center;color:var(--white)}
.feature-icon{width:82px;height:82px;border-radius:50%;background:var(--ink);border:3px solid var(--white);margin:0 auto;display:flex;align-items:center;justify-content:center}
.feature h4{font-size:17px;font-weight:700;margin-top:22px;line-height:1.3}
.feature p{font-size:14.5px;line-height:1.55;margin-top:10px;padding:0 40px;color:#e7f0fa}
.feature-divider{position:absolute;top:532px;width:1px;height:225px;background:rgba(255,255,255,.35)}
.slider-arrow{position:absolute;top:626px}

/* testimonials */
.testimonial{position:absolute;top:2449px;width:331px;height:203px;background:#eeeeee;padding:24px 30px;text-align:center}
.testimonial p{font-size:14px;font-style:italic;color:var(--muted);line-height:1.65}
.testimonial .who{color:var(--blue);font-weight:700;font-size:13px;margin-top:14px;text-transform:uppercase}
.quote-mark{position:absolute;font-size:90px;font-weight:800;color:#d8d8d8;line-height:1}
.avatar{position:absolute;top:2615px;width:76px;height:76px;border-radius:50%;border:3px solid var(--white);background:linear-gradient(#cfd3d6,#8f969c)}
.dots{position:absolute;left:572px;top:2730px;display:flex;gap:7px}
.dots i{width:13px;height:13px;border-radius:50%;background:#555}
.dots i.on{background:var(--blue)}

/* partners */
.partners{position:absolute;left:0;top:2792px;width:1200px;height:196px;background:var(--light)}
.partner-badge{position:absolute;top:100px;height:54px;background:#9aa3ad;border-radius:6px}

/* schedule */
.schedule{position:absolute;left:0;top:2988px;width:1200px;height:338px;background:var(--dark)}
.schedule .section-title{color:var(--white);top:48px}
.field{position:absolute;width:331px;height:40px;background:var(--white);font-size:13px;color:#555;padding:0 16px;display:flex;align-items:center}
.btn-green{position:absolute;left:497px;top:237px;width:208px;height:49px;background:var(--green);color:var(--white);font-weight:700;font-size:15px;display:flex;align-items:center;justify-content:center;text-transform:uppercase}

/* footer */
.site-footer{position:absolute;left:0;top:3326px;width:1200px;height:284px;background:var(--blue);color:var(--white)}
.footer-brand{position:absolute;left:76px;top:50px;display:flex;align-items:center;gap:10px}
.footer-brand .brand-dot{width:36px;height:36px;background:var(--white)}
.footer-brand .brand-name{color:var(--white);font-size:28px}
.offices{position:absolute;left:76px;top:128px;font-size:12.5px;line-height:22px}
.offices td:first-child{padding-right:26px}
.footer-col h5{font-size:13px;font-weight:700;text-transform:uppercase;margin-bottom:14px}
.footer-col ul{list-style:none;font-size:13px;line-height:31px}
.post{display:flex;gap:14px;margin-bottom:20px}
.post-thumb{width:76px;height:54px;background:linear-gradient(#dfe5ea,#aeb8c1);flex:none}
.post b{display:block;font-size:13px;font-weight:700}
.post span{font-size:12px;line-height:1.5;display:block}
.signup-field{width:240px;height:40px;background:var(--white);color:#777;font-size:12.5px;display:flex;align-items:center;padding:0 14px}
.signup-btn{margin:20px 0 0 152px;width:88px;height:40px;background:#111;font-size:13px;font-weight:700;display:flex;align-items:center;justify-content:center;text-transform:uppercase}
.bottom-bar{position:absolute;left:0;top:3610px;width:1200px;height:63px;background:var(--darker);color:#999;font-size:12px}
.bottom-bar .copy{position:absolute;left:76px;top:24px}
.socials{position:absolute;left:955px;top:20px;display:flex;gap:16px}
.socials i{width:20px;height:20px;border-radius:50%;background:#ddd;display:block}
</style>
</head>
<body>

<header class="site-header">
  <div class="brand"><span class="brand-dot"></span><span class="brand-name">Corvane IT</span></div>
  <div class="header-cta">Schedule a free network assessment today!</div>
  <div class="header-phone">
    <span class="phone-badge"><svg width="18" height="18" viewBox="0 0 24 24"><path fill="#fff" d="M6.6 10.8a15.2 15.2 0 0 0 6.6 6.6l2.2-2.2a1 1 0 0 1 1-.25 11.4 11.4 0 0 0 3.6.57 1 1 0 0 1 1 1V20a1 1 0 0 1-1 1A17 17 0 0 1 3 4a1 1 0 0 1 1-1h3.5a1 1 0 0 1 1 1c0 1.25.2 2.45.57 3.57a1 1 0 0 1-.25 1z"/></svg></span>
    555-310- 4400
  </div>
  <nav class="main-nav">
    <a class="active" href="#">Home</a><a href="#">Data</a><a href="#">Cloud</a><a href="#">Voice</a><a href="#">Contact</a>
  </nav>
</header>

<section class="hero" role="img" aria-label="Office desk with a black business desk phone in the foreground, blurred workplace behind">
  <div class="hero-caption">
    <h1>Business <span>Phone Systems</span></h1>
    <p>We are an IT support company that provides commercial IT support and services to small and medium sized businesse.</p>
  </div>
  <div class="hero-dots"><i></i><i></i><i class="on"></i></div>
</section>

<h2 class="section-title" style="top:720px;font-size:25px">Our Services</h2>

<svg width="0" height="0" style="position:absolute"><defs>
  <symbol id="tick" viewBox="0 0 14 14"><path d="M2 7.5l3 3 7-7" fill="none" stroke="#1a73c4" stroke-width="2.4"/></symbol>
</defs></svg>

<article class="service-card" style="left:73px">
  <div class="service-head">
    <svg width="50" height="58" viewBox="0 0 50 58"><g fill="#333"><ellipse cx="25" cy="9" rx="23" ry="8"/><path d="M2 15c0 5 10 9 23 9s23-4 23-9v11c0 5-10 9-23 9S2 31 2 26z"/><path d="M2 33c0 5 10 9 23 9s23-4 23-9v14c0 5-10 9-23 9S2 52 2 47z"/></g></svg>
    <h3>Data</h3>
  </div>
  <ul class="service-list">
    <li><svg class="tick"><use href="#tick"/></svg>Managed IT Services</li>
    <li><svg class="tick"><use href="#tick"/></svg>IT Support &amp; Consulting</li>
    <li><svg class="tick"><use href="#tick"/></svg>IT Helpdesk Services</li>
    <li><svg class="tick"><use href="#tick"/></svg>Network Security</li>
    <li><svg class="tick"><use href="#tick"/></svg>Data Backup &amp; Recovery</li>
  </ul>
  <span class="btn-small">Read more</span>
</article>

<article class="service-card" style="left:436px">
  <div class="service-head">
    <svg width="68" height="46" viewBox="0 0 68 46"><path fill="#333" d="M16 46a15 15 0 0 1-2-29.9A20 20 0 0 1 52 13a16.5 16.5 0 0 1 0 33z"/></svg>
    <h3>Cloud</h3>
  </div>
  <ul class="service-list">
    <li><svg class="tick"><use href="#tick"/></svg>Office Suite Migrations</li>
    <li><svg class="tick"><use href="#tick"/></svg>Cloud Host Management Services</li>
    <li><svg class="tick"><use href="#tick"/></svg>Cloud Migration Services</li>
    <li><svg class="tick"><use href="#tick"/></svg>Hosted Virtual Servers</li>
    <li><svg class="tick"><use href="#tick"/></svg>Hosted Telephone Systems</li>
  </ul>
  <span class="btn-small">Read more</span>
</article>

<article class="service-card" style="left:796px">
  <div class="service-head">
    <svg width="50" height="50" viewBox="0 0 24 24"><path fill="#333" d="M6.6 10.8a15.2 15.2 0 0 0 6.6 6.6l2.2-2.2a1 1 0 0 1 1-.25 11.4 11.4 0 0 0 3.6.57 1 1 0 0 1 1 1V20a1 1 0 0 1-1 1A17 17 0 0 1 3 4a1 1 0 0 1 1-1h3.5a1 1 0 0 1 1 1c0 1.25.2 2.45.57 3.57a1 1 0 0 1-.25 1z"/></svg>
    <h3>Voice</h3>
  </div>
  <ul class="service-list">
    <li><svg class="tick"><use href="#tick"/></svg>Open PBX Consulting</li>
    <li><svg class="tick"><use href="#tick"/></svg>Business Telephone Systems</li>
    <li><svg class="tick"><use href="#tick"/></svg>Multiple Office Phone Systems</li>
    <li><svg class="tick"><use href="#tick"/></svg>Desk Handset Telephone Systems</li>
    <li><svg class="tick"><use href="#tick"/></svg>SIP Trunks</li>
  </ul>
  <span class="btn-small">Read more</span>
</article>

<section class="welcome">
  <div class="welcome-photo" role="img" aria-label="Support team wearing headsets working at computers in a bright call centre"></div>
  <div class="welcome-copy">
    <h2>Welcome to our website</h2>
    <p>Technology is the backbone of your business. Corvane IT excels at providing outsourced network IT support to businesses just like yours. Our team of friendly and highly experienced engineers are standing by to help you get the most out of your technology.</p>
    <span class="btn">Read more</span>
  </div>
</section>

<section class="why">
  <h2 class="section-title">Why Corvane IT</h2>
  <div class="video-frame" role="img" aria-label="Video still: hands holding a tablet showing a smiling support agent with a headset">
    <svg class="play" width="60" height="60" viewBox="0 0 60 60"><circle cx="30" cy="30" r="28" fill="rgba(255,255,255,.9)"/><path d="M24 18l18 12-18 12z" fill="#1a73c4"/></svg>
  </div>

  <svg class="slider-arrow" style="left:46px" width="16" height="24" viewBox="0 0 16 24"><path d="M12 3L4 12l8 9" fill="none" stroke="#fff" stroke-width="3"/></svg>
  <svg class="slider-arrow" style="left:1138px" width="16" height="24" viewBox="0 0 16 24"><path d="M4 3l8 9-8 9" fill="none" stroke="#fff" stroke-width="3"/></svg>

  <div class="feature" style="left:63px">
    <div class="feature-icon"><svg width="36" height="36" viewBox="0 0 36 36"><g fill="none" stroke="#fff" stroke-width="3"><circle cx="13" cy="20" r="6"/><circle cx="27" cy="10" r="4"/></g><g stroke="#fff" stroke-width="3"><path d="M13 10v3M13 27v3M3 20h3M20 20h3M27 3v2M27 15v2M20 10h2M32 10h2"/></g></svg></div>
    <h4>Control IT Spending</h4>
    <p>We offer an all-inclusive proactive, reliable, and affordable solution for your IT support needs..</p>
  </div>
  <div class="feature-divider" style="left:421px"></div>
  <div class="feature" style="left:421px">
    <div class="feature-icon"><svg width="36" height="36" viewBox="0 0 36 36"><path d="M4 4v28h28" fill="none" stroke="#fff" stroke-width="3"/><path d="M9 25l7-8 5 5 9-11" fill="none" stroke="#fff" stroke-width="3"/></svg></div>
    <h4>Optimized IT Efficiency</h4>
    <p>Technology is not a one size fits all approach. Corvane IT determines and implements solutions...</p>
  </div>
  <div class="feature-divider" style="left:779px"></div>
  <div class="feature" style="left:779px">
    <div class="feature-icon"><svg width="36" height="36" viewBox="0 0 36 36"><g fill="#fff"><rect x="13" y="3" width="10" height="8"/><rect x="2" y="25" width="10" height="8"/><rect x="13" y="25" width="10" height="8"/><rect x="24" y="25" width="10" height="8"/></g><path d="M18 11v14M7 25v-6h22v6" fill="none" stroke="#fff" stroke-width="2.5"/></svg></div>
    <h4>Real Proactive Network<br>Management</h4>
    <p>Our approach to IT support and network management is based upon a proven checklist..</p>
  </div>
</section>

<h2 class="section-title" style="top:2388px;font-size:25px">Customer Testimonials</h2>

<div class="testimonial" style="left:73px"><span class="quote-mark" style="left:12px;top:6px">&ldquo;</span><span class="quote-mark" style="right:16px;top:120px">&rdquo;</span><p>Aliquam molestie, mi et imperdiet euismod, dui purus auctor tellus, et interdum lacus lectus et ante. Sed accumsan sollicitudin sapien, sit amet adipiscing turpis...</p><div class="who">-Name Heading</div></div>
<div class="testimonial" style="left:436px"><span class="quote-mark" style="left:12px;top:6px">&ldquo;</span><span class="quote-mark" style="right:16px;top:120px">&rdquo;</span><p>Aliquam molestie, mi et imperdiet euismod, dui purus auctor tellus, et interdum lacus lectus et ante. Sed accumsan sollicitudin sapien, sit amet adipiscing turpis...</p><div class="who">-Name Heading</div></div>
<div class="testimonial" style="left:796px"><span class="quote-mark" style="left:12px;top:6px">&ldquo;</span><span class="quote-mark" style="right:16px;top:120px">&rdquo;</span><p>Aliquam molestie, mi et imperdiet euismod, dui purus auctor tellus, et interdum lacus lectus et ante. Sed accumsan sollicitudin sapien, sit amet adipiscing turpis...</p><div class="who">-Name Heading</div></div>
<div class="avatar" style="left:201px" role="img" aria-label="Customer portrait"></div>
<div class="avatar" style="left:564px" role="img" aria-label="Customer portrait"></div>
<div class="avatar" style="left:924px" role="img" aria-label="Customer portrait"></div>
<div class="dots"><i class="on"></i><i></i><i></i></div>

<section class="partners">
  <h2 class="section-title" style="top:38px;font-size:25px">Our Partners</h2>
  <div class="partner-badge" style="left:78px;width:92px" role="img" aria-label="Partner badge"></div>
  <div class="partner-badge" style="left:215px;width:136px" role="img" aria-label="Partner badge"></div>
  <div class="partner-badge" style="left:398px;width:106px" role="img" aria-label="Partner badge"></div>
  <div class="partner-badge" style="left:543px;width:224px" role="img" aria-label="Partner badge"></div>
  <div class="partner-badge" style="left:800px;width:180px" role="img" aria-label="Partner badge"></div>
  <div class="partner-badge" style="left:1016px;width:98px" role="img" aria-label="Partner badge"></div>
</section>

<section class="schedule">
  <h2 class="section-title">Schedule a free network assessment today</h2>
  <div class="field" style="left:255px;top:117px">Name</div>
  <div class="field" style="left:617px;top:117px">Company Name</div>
  <div class="field" style="left:255px;top:171px">Email Address</div>
  <div class="field" style="left:617px;top:171px">Phone No.</div>
  <div class="btn-green">Schedule now</div>
</section>

<footer class="site-footer">
  <div class="footer-brand"><span class="brand-dot"></span><span class="brand-name">Corvane IT</span></div>
  <table class="offices">
    <tr><td>Main Number:</td><td>555-310-4400</td></tr>
    <tr><td>Houston:</td><td>555-310-4410</td></tr>
    <tr><td>San Antonio:</td><td>555-310-4420</td></tr>
    <tr><td>Austin:</td><td>555-310-4430</td></tr>
    <tr><td>Tulsa:</td><td>555-310-4440</td></tr>
    <tr><td>Oklahoma City:</td><td>555-310-4450</td></tr>
  </table>
  <div class="footer-col abs" style="left:368px;top:54px">
    <h5>Site Map</h5>
    <ul><li>Home</li><li>Services</li><li>Why Corvane IT</li><li>Contact us</li></ul>
  </div>
  <div class="footer-col abs" style="left:533px;top:54px;width:330px">
    <h5>Blog Posts</h5>
    <div class="post"><div class="post-thumb" role="img" aria-label="Blog post thumbnail"></div><div><b>Consectetuer adipiscing elit</b><span>Aenean a nibh eget turpis vehicula tempus ac...</span></div></div>
    <div class="post"><div class="post-thumb" role="img" aria-label="Blog post thumbnail"></div><div><b>Consectetuer adipiscing elit</b><span>Aenean a nibh eget turpis vehicula tempus ac...</span></div></div>
  </div>
  <div class="footer-col abs" style="left:885px;top:54px">
    <h5>Email Sign Up</h5>
    <div class="signup-field">Enter Email Address</div>
    <div class="signup-btn">Sign up</div>
  </div>
</footer>

<div class="bottom-bar">
  <span class="copy">Copyright © 2017, Company Name. All Right Reserved</span>
  <div class="socials" aria-label="Social links"><i></i><i></i><i></i><i></i><i></i></div>
</div>

</body>
</html>
```